Signage Design Project

We need a logo and signage for the shopfront of a personal fitness training gym and coaching facility. We want the signage to cover the glass shopfront windows which consist of 4 glass windows with dimensions: 1 of 200cm x 180cm, 2 of 180cm x 135cm and 1 of 180cm x 180cm. The windows that are 200x 180 and 180x180 are the most visable/ important. We want the 200x180 to display the logo and our name which is "Ridgeline Fitness Centre" with further information of: Your personal training studio and boutique coaching gym Ph: 9471 2836.
For the window with 180 x 180cm measurement we want to list the services we provide which are:
Personal Training Sessions | Group Classes|Weight Loss |Toning & Sculpting|Bodybuilding I Cardio|Weights| Kettlebells| Boxing| Circuits I Team Building Programs| Boot Camp I Healthy Lifestyle & Wellness Coaching
The 2 windows 180x135cm are diagonal to the entry of the shop. We want them to be the same and plainer in design with the words: Ridgeline Fitness Centre
Personal Training Studio and Boutique Coaching Gym
The signage design also includes an acrylic window box that lights up which is to display the logo and Ridgeline Fitness Centre

```html
<!DOCTYPE html>
<html lang="en">
<head>
<meta charset="utf-8">
<title>Ridgeline Fitness Centre — Window Signage</title>
<link rel="stylesheet" href="https://fonts.googleapis.com/css2?family=Arimo:wght@700&display=swap">
<style>
  :root {
    --page: #ffffff;
    --frame: #4a4a4a;
    --brand-cyan: #0b9cc2;
    --lime: #a6b820;
    --teal: #0a7088;
    --photo-light: #eef1f3;
    --photo-blue: #bfe0ef;
  }
  * { margin: 0; padding: 0; box-sizing: border-box; }
  html, body {
    width: 1200px;
    height: 900px;
    overflow: hidden;
    background: var(--page);
  }
  .sign {
    position: absolute;
    left: 327px;
    top: 93px;
    width: 535px;
    height: 719px;
    border: 1px solid var(--frame);
    background: var(--page);
    overflow: hidden;
    font-family: "Arimo", Arial, sans-serif;
    font-weight: 700;
  }
  .brand {
    position: absolute;
    left: 60px;
    top: 128px;
    display: flex;
    align-items: center;
    gap: 16px;
  }
  .brand-dot {
    width: 96px;
    height: 96px;
    border-radius: 50%;
    background: var(--brand-cyan);
    flex: none;
  }
  .brand-name {
    color: var(--brand-cyan);
    line-height: 1;
  }
  .brand-name .primary {
    display: block;
    font-size: 52px;
    letter-spacing: 1px;
  }
  .brand-name .secondary {
    display: block;
    font-size: 31px;
    letter-spacing: 2.5px;
    margin-top: 6px;
  }
  .tagline {
    position: absolute;
    left: 0;
    right: 0;
    top: 310px;
    text-align: center;
  }
  .tagline .service {
    display: block;
    color: var(--lime);
    font-size: 32px;
    letter-spacing: 1.2px;
  }
  .tagline .venue {
    display: block;
    color: var(--teal);
    font-size: 24px;
    letter-spacing: 1.2px;
    margin-top: 2px;
  }
  .tagline .amp { color: var(--lime); }
  .swoosh {
    position: absolute;
    left: 0;
    top: 0;
    width: 535px;
    height: 719px;
  }
</style>
</head>
<body>
  <main class="sign">
    <svg class="swoosh" viewBox="0 0 535 719" aria-hidden="true">
      <path class="band-lime" d="M0,482 C110,585 280,655 440,638 L535,622 L535,719 L0,719 Z" fill="var(--lime)"/>
      <path class="band-teal" d="M535,432 C505,565 420,680 285,719 L535,719 Z" fill="var(--teal)"/>
      <path class="band-line" d="M0,538 C140,675 300,722 440,648" fill="none" stroke="#ffffff" stroke-width="6"/>
    </svg>

    <div class="brand">
      <span class="brand-dot"></span>
      <span class="brand-name">
        <span class="primary">RIDGELINE</span>
        <span class="secondary">Fitness Centre</span>
      </span>
    </div>

    <p class="tagline">
      <span class="service">Personal Training</span>
      <span class="venue">Studio <span class="amp">&amp;</span> Boutique Coaching Gym</span>
    </p>

    <svg class="swoosh" viewBox="0 0 535 719">
      <defs>
        <linearGradient id="athlete-tones" x1="0" y1="0" x2="0" y2="1">
          <stop offset="0" stop-color="var(--photo-light)"/>
          <stop offset="1" stop-color="var(--photo-blue)"/>
        </linearGradient>
      </defs>
      <rect class="athlete-photo" x="113" y="447" width="325" height="265" fill="url(#athlete-tones)"
            role="img" aria-label="Photo of a smiling woman in a blue tank top and running shoes, seated and stretching"/>
    </svg>
  </main>
</body>
</html>
```